Real Estate Company Looking for Business Card Designs for 3 Executives

Hello!
Thanks so much for considering our project! We are a real estate investment company located in Edmonton, Alberta called Bellhaven Group of Companies. We invest/develop both commercial and residential real estate and are looking to create 3 DOUBLE-SIDED business cards for 3 top executives in the company! (for some reason it won't let us select the double-sided option, but yes, the cards are double sided and would be happy to tip extra)

We have certain guidelines that we want our business cards to for sure follow - the back of the Business card has to be the Black Background Version of the Logo which has already been designed and linked as a file (first file). We want the entire back of the card to simply just be the black background logo. In terms of the front of the card, would like to see a smaller version of the white background logo (linked as the second file) in the top left hand corner - of course, feel free to get creative and we can make revisions together along the way! and Then after that, just text. We want the card to be sharp, clean, easy on the eyes and highly professional looking. We would like the card to include the Full name of the Company (Bellhaven Group of Companies), Name of the Person, Title, Phone, Email. If possible please provide the front part of the card for 3 people:

1) Bellhaven Group of Companies, Liora Quenby, Chief Financial Officer, 780-555-0142, lioraquenby@bellhavengroup.example

2) Bellhaven Group of Companies, Tobias Quenby, Chief Executive Officer, 780-555-0187, tobiasquenby@bellhavengroup.example

3) Bellhaven Group of Companies, Rui Delcourt, Chief Operations Officer, 587-555-0163, ruidelcourt@bellhavengroup.example

Thank you so much for considering our project & we look forward to seeing your designs!

```html
<!DOCTYPE html>
<html lang="en">
<head>
<meta charset="utf-8">
<title>Bellhaven Group of Companies – Executive Business Cards</title>
<link rel="stylesheet" href="https://fonts.googleapis.com/css2?family=Arimo:wght@400;700&display=swap">
<style>
  :root {
    --backdrop: #e4e4e2;
    --card: #2f2f30;
    --card-shade: #3a393a;
    --ink: #ffffff;
    --ink-soft: #e2e2e2;
  }
  * { margin: 0; padding: 0; box-sizing: border-box; }
  html, body {
    width: 1200px;
    height: 801px;
    overflow: hidden;
    background: var(--backdrop);
    font-family: "Arimo", Arial, sans-serif;
  }
  .canvas {
    position: relative;
    width: 1200px;
    height: 801px;
  }
  .card {
    position: absolute;
    background: var(--card);
    color: var(--ink);
    overflow: hidden;
    box-shadow: 0 6px 18px rgba(0, 0, 0, 0.18);
  }

  /* Fronts (portrait) */
  .card-front {
    top: 182px;
    width: 250px;
    height: 437px;
  }
  .card-front--cfo { left: 30px; }
  .card-front--ceo { left: 300px; }
  .card-front--coo { left: 570px; }

  .card-front .forest {
    position: absolute;
    left: 0;
    top: 0;
    width: 100%;
    height: 190px;
    background: linear-gradient(180deg, var(--card-shade) 0%, var(--card) 100%);
  }
  .card-front .card-body {
    position: absolute;
    left: 22px;
    right: 22px;
    top: 212px;
    display: flex;
    flex-direction: column;
  }
  .wordmark {
    display: flex;
    align-items: center;
  }
  .card-front .wordmark { gap: 9px; }
  .card-front .wordmark-dot {
    width: 11px;
    height: 11px;
    border-radius: 50%;
    background: var(--ink);
  }
  .card-front .wordmark-name {
    font-size: 16px;
    font-weight: 400;
    letter-spacing: 5px;
    color: var(--ink);
  }
  .person { margin-top: 30px; }
  .person-name {
    font-size: 16px;
    font-weight: 700;
    letter-spacing: 0.4px;
    text-transform: uppercase;
  }
  .person-title {
    margin-top: 3px;
    font-size: 12.5px;
    font-weight: 400;
    color: var(--ink-soft);
  }
  .company-name {
    margin-top: 8px;
    font-size: 11px;
    font-weight: 400;
    color: var(--ink-soft);
  }
  .contact {
    margin-top: 26px;
    list-style: none;
    font-size: 10px;
    color: var(--ink-soft);
  }
  .contact-item {
    display: flex;
    align-items: center;
    gap: 7px;
    margin-bottom: 7px;
    white-space: nowrap;
  }
  .contact-icon {
    width: 11px;
    height: 11px;
    flex: none;
  }

  /* Back (landscape) */
  .card-back {
    left: 840px;
    top: 306px;
    width: 330px;
    height: 189px;
  }
  .card-back .forest {
    position: absolute;
    right: 0;
    top: 0;
    width: 140px;
    height: 100%;
    background: linear-gradient(90deg, var(--card) 0%, var(--card-shade) 45%, var(--card) 100%);
  }
  .card-back .wordmark {
    position: absolute;
    left: 36px;
    top: 83px;
    gap: 10px;
  }
  .card-back .wordmark-dot {
    width: 13px;
    height: 13px;
    border-radius: 50%;
    background: var(--ink);
  }
  .card-back .wordmark-name {
    font-size: 18px;
    font-weight: 400;
    letter-spacing: 6px;
    color: var(--ink);
  }
</style>
</head>
<body>
<main class="canvas">

  <section class="card card-front card-front--cfo" aria-label="Business card front, Chief Financial Officer">
    <div class="forest" role="img" aria-label="Faint pine tree silhouettes in dark grey"></div>
    <div class="card-body">
      <div class="wordmark"><span class="wordmark-dot"></span><span class="wordmark-name">BELLHAVEN</span></div>
      <div class="person">
        <p class="person-name">Liora Quenby</p>
        <p class="person-title">Chief Financial Officer</p>
        <p class="company-name">Bellhaven Group of Companies</p>
      </div>
      <ul class="contact">
        <li class="contact-item">
          <svg class="contact-icon" viewBox="0 0 24 24" aria-hidden="true"><path fill="#ffffff" d="M6.6 10.8a15.1 15.1 0 0 0 6.6 6.6l2.2-2.2a1 1 0 0 1 1-.25 11.4 11.4 0 0 0 3.6.57 1 1 0 0 1 1 1V20a1 1 0 0 1-1 1A17 17 0 0 1 3 4a1 1 0 0 1 1-1h3.5a1 1 0 0 1 1 1c0 1.25.2 2.45.57 3.57a1 1 0 0 1-.25 1z"/></svg>
          <span>780-555-0142</span>
        </li>
        <li class="contact-item">
          <svg class="contact-icon" viewBox="0 0 24 24" aria-hidden="true"><rect x="2.5" y="5" width="19" height="14" rx="1.5" fill="none" stroke="#ffffff" stroke-width="2"/><path d="M3 6l9 7 9-7" fill="none" stroke="#ffffff" stroke-width="2"/></svg>
          <span>lioraquenby@bellhavengroup.example</span>
        </li>
      </ul>
    </div>
  </section>

  <section class="card card-front card-front--ceo" aria-label="Business card front, Chief Executive Officer">
    <div class="forest" role="img" aria-label="Faint pine tree silhouettes in dark grey"></div>
    <div class="card-body">
      <div class="wordmark"><span class="wordmark-dot"></span><span class="wordmark-name">BELLHAVEN</span></div>
      <div class="person">
        <p class="person-name">Tobias Quenby</p>
        <p class="person-title">Chief Executive Officer</p>
        <p class="company-name">Bellhaven Group of Companies</p>
      </div>
      <ul class="contact">
        <li class="contact-item">
          <svg class="contact-icon" viewBox="0 0 24 24" aria-hidden="true"><path fill="#ffffff" d="M6.6 10.8a15.1 15.1 0 0 0 6.6 6.6l2.2-2.2a1 1 0 0 1 1-.25 11.4 11.4 0 0 0 3.6.57 1 1 0 0 1 1 1V20a1 1 0 0 1-1 1A17 17 0 0 1 3 4a1 1 0 0 1 1-1h3.5a1 1 0 0 1 1 1c0 1.25.2 2.450.57 3.57a1 1 0 0 1-.25 1z"/></svg>
          <span>780-555-0187</span>
        </li>
        <li class="contact-item">
          <svg class="contact-icon" viewBox="0 0 24 24" aria-hidden="true"><rect x="2.5" y="5" width="19" height="14" rx="1.5" fill="none" stroke="#ffffff" stroke-width="2"/><path d="M3 6l9 7 9-7" fill="none" stroke="#ffffff" stroke-width="2"/></svg>
          <span>tobiasquenby@bellhavengroup.example</span>
        </li>
      </ul>
    </div>
  </section>

  <section class="card card-front card-front--coo" aria-label="Business card front, Chief Operations Officer">
    <div class="forest" role="img" aria-label="Faint pine tree silhouettes in dark grey"></div>
    <div class="card-body">
      <div class="wordmark"><span class="wordmark-dot"></span><span class="wordmark-name">BELLHAVEN</span></div>
      <div class="person">
        <p class="person-name">Rui Delcourt</p>
        <p class="person-title">Chief Operations Officer</p>
        <p class="company-name">Bellhaven Group of Companies</p>
      </div>
      <ul class="contact">
        <li class="contact-item">
          <svg class="contact-icon" viewBox="0 0 24 24" aria-hidden="true"><path fill="#ffffff" d="M6.6 10.8a15.1 15.1 0 0 0 6.6 6.6l2.2-2.2a1 1 0 0 1 1-.25 11.4 11.4 0 0 0 3.6.57 1 1 0 0 1 1 1V20a1 1 0 0 1-1 1A17 17 0 0 1 3 4a1 1 0 0 1 1-1h3.5a1 1 0 0 1 1 1c0 1.25.2 2.45.57 3.57a1 1 0 0 1-.25 1z"/></svg>
          <span>587-555-0163</span>
        </li>
        <li class="contact-item">
          <svg class="contact-icon" viewBox="0 0 24 24" aria-hidden="true"><rect x="2.5" y="5" width="19" height="14" rx="1.5" fill="none" stroke="#ffffff" stroke-width="2"/><path d="M3 6l9 7 9-7" fill="none" stroke="#ffffff" stroke-width="2"/></svg>
          <span>ruidelcourt@bellhavengroup.example</span>
        </li>
      </ul>
    </div>
  </section>

  <section class="card card-back" aria-label="Business card back">
    <div class="forest" role="img" aria-label="Faint pine tree silhouettes in dark grey"></div>
    <div class="wordmark">
      <span class="wordmark-dot"></span>
      <span class="wordmark-name">BELLHAVEN</span>
    </div>
  </section>

</main>
</body>
</html>
```